Velmoria-Quillmesh Partial Redesign - Web App

Are you able to apply your creativity to an existing layout? I’m convinced that even just a few touches can make a big difference to add personality and professionalism to a website design, and I’m looking for someone able to use existing ideas and bring them to the next level while keeping inside some given constraints.
The actual job is to improve an existing design concept and to apply it creatively to a landing page, a simple home page, and an older web app (single page website).
To help you start with a clear picture of the current situation and of my requirements, I created a detailed brief with screenshots, live examples, and complete instructions. You can find it attached to this job.
My tastes are inclined towards clean and simple designs. For this project I'm not looking for dazzling novelty, but for very solid craftsmanship. Are the right man - or woman - for the job?
Updates
I wanted to thank everybody who participated in this project. I made a choice, but also other designs were interesting. Hope to work with you another time.
Target Market(s)
Our main target is social media marketers and startuppers
Look and feel
Each slider illustrates characteristics of the customer's brand and the style your logo design should communicate.

```html
<!DOCTYPE html>
<html lang="en">
<head>
<meta charset="utf-8">
<title>Velmoria – #hashtags</title>
<link rel="stylesheet" href="https://fonts.googleapis.com/css2?family=Cabin:wght@400;500;700&family=Open+Sans:ital,wght@0,400;1,400&display=swap">
<style>
:root{
  --ink:#1f2126;
  --dark:#2d323b;
  --dark-2:#1c2027;
  --sky:#9dd3fb;
  --sky-deep:#8cc8f4;
  --accent:#8dc9f0;
  --page:#f1f1f1;
  --line:#3a3f48;
  --muted:#7a7a7a;
  --link:#2a6db8;
  --chart:#d42a2a;
}
*{box-sizing:border-box;margin:0;padding:0}
html,body{width:1200px;height:990px;overflow:hidden}
body{position:relative;background:var(--page);font-family:"Cabin",sans-serif;color:var(--ink)}
.abs{position:absolute}
.topbar{left:0;top:0;width:1200px;height:8px;background:var(--dark)}
.account-btn{top:8px;height:15px;background:var(--dark);color:#fff;font-size:8px;line-height:15px;text-align:center;box-shadow:0 1px 2px rgba(0,0,0,.3)}
.header{left:0;top:36px;width:1200px;height:77px;background:var(--sky);box-shadow:0 1px 3px rgba(0,0,0,.15)}
.brand{left:306px;top:57px;display:flex;align-items:center;gap:8px;height:26px}
.brand-mark{width:14px;height:14px;background:var(--dark)}
.brand-name{font-size:26px;font-weight:700;color:var(--dark);line-height:26px}
.brand-tag{left:336px;top:82px;font-size:8px;line-height:10px;color:var(--dark)}
.nav{left:513px;top:68px;font-size:10.5px}
.nav a{color:var(--dark);text-decoration:none;position:absolute;white-space:nowrap}
.nav a.active{color:#fff}
.search{left:848px;top:64px;width:112px;height:21px;background:#fff;border:1px solid #5c8fb6}
.search-btn{right:0;top:0;width:21px;height:19px;border-left:1px solid #5c8fb6}
.title{left:240px;top:147px;font-size:16px;font-weight:500}
.meta{left:240px;font-size:9.5px}
.diagram{left:280px;top:210px;width:380px;height:380px}
.mode-toggle{left:375px;top:614px;width:181px;height:30px;border-radius:3px;overflow:hidden;box-shadow:0 2px 3px rgba(0,0,0,.3)}
.section-title{font-size:17px;color:var(--accent);font-weight:400}
.users{left:250px;top:708px;list-style:none;font-size:10.5px;line-height:18px}
.chart{left:396px;top:716px;width:300px;height:188px}
.follow-btn{left:735px;width:97px;height:22px;background:var(--dark);color:#fff;font-size:10px;line-height:22px}
.follow-btn .ico{position:absolute;left:10px;top:6px;width:10px;height:10px;background:#fff}
.follow-btn span{position:absolute;left:32px}
.followers{left:859px;font-size:10px;line-height:22px}
.counter-box{left:735px;top:278px;width:225px;height:89px;background:var(--sky)}
.digit{top:313px;width:18px;height:20px;background:#fff;font-size:13px;font-weight:700;text-align:center;line-height:20px;color:var(--dark)}
.avatar{left:735px;width:35px;height:35px;border:2px solid #fff;box-shadow:0 0 1px rgba(0,0,0,.4)}
.avatar-name{left:735px;width:35px;text-align:center;font-family:"Open Sans",sans-serif;font-style:italic;font-size:7.5px}
.bubble{left:783px;width:177px;height:52px;background:#fff;border:1px solid #d6d6d6;font-family:"Open Sans",sans-serif;font-size:7.3px;color:var(--muted);padding:5px 7px;line-height:15px}
.bubble em{color:var(--link);display:block}
.footer-fade{left:0;top:912px;width:1200px;height:34px;background:linear-gradient(#f1f1f1,#dcdcdc)}
.footer{left:0;top:946px;width:1200px;height:44px;background:var(--dark);color:#c8c8c8;font-size:9px}
</style>
</head>
<body>
<div class="abs topbar"></div>
<div class="abs account-btn" style="left:240px;width:45px">Login</div>
<div class="abs account-btn" style="left:293px;width:45px">Sign up!</div>

<header class="abs header"></header>
<div class="abs brand"><span class="brand-mark"></span><span class="brand-name">Velmoria</span></div>
<div class="abs brand-tag">Networked Audience Intelligence</div>
<nav class="abs nav">
  <a class="active" style="left:0">Home</a><a style="left:45px">About</a><a style="left:95px">Blog</a>
  <a style="left:137px">Timeline</a><a style="left:197px">Influencers</a><a style="left:267px">Hashtags</a>
</nav>
<div class="abs search"><div class="abs search-btn"><svg width="20" height="19" viewBox="0 0 20 19"><circle cx="9" cy="8" r="4" fill="none" stroke="#2d6a9a" stroke-width="1.6"/><line x1="12" y1="11" x2="15" y2="14" stroke="#2d6a9a" stroke-width="2"/></svg></div></div>

<h1 class="abs title">#hashtags</h1>
<p class="abs meta" style="top:171px">Variants:&nbsp; hashtags: 80%&nbsp;&nbsp; Hashtags: 14%&nbsp;&nbsp; HASHTAGS: 3%&nbsp;&nbsp; HashTags: 3%&nbsp;&nbsp; hashTags: 0%</p>
<p class="abs meta" style="top:189px">Popularity: 57.7</p>

<svg class="abs diagram" viewBox="345 262 475 475" font-family="Cabin, sans-serif">
  <defs>
    <polygon id="oct" points="0.383,-0.924 0.924,-0.383 0.924,0.383 0.383,0.924 -0.383,0.924 -0.924,0.383 -0.924,-0.383 -0.383,-0.924"/>
    <linearGradient id="nodeFill" x1="0" y1="0" x2="0" y2="1"><stop offset="0" stop-color="#4a505b"/><stop offset="1" stop-color="#15181d"/></linearGradient>
    <radialGradient id="hubFill" cx="0.5" cy="0.45" r="0.6"><stop offset="0" stop-color="#d8efff"/><stop offset="1" stop-color="#7cc3f5"/></radialGradient>
  </defs>
  <g stroke="var(--line)" stroke-width="3">
    <line x1="572" y1="520" x2="572" y2="315"/><line x1="572" y1="520" x2="461" y2="368"/>
    <line x1="572" y1="520" x2="665" y2="390"/><line x1="572" y1="520" x2="750" y2="462"/>
    <line x1="572" y1="520" x2="434" y2="476"/><line x1="572" y1="520" x2="716" y2="566"/>
    <line x1="572" y1="520" x2="406" y2="573"/><line x1="572" y1="520" x2="469" y2="660"/>
    <line x1="572" y1="520" x2="572" y2="693"/><line x1="572" y1="520" x2="691" y2="683"/>
  </g>
  <g fill="url(#nodeFill)">
    <use href="#oct" transform="translate(572 315) scale(46)"/><use href="#oct" transform="translate(461 368) scale(43)"/>
    <use href="#oct" transform="translate(665 390) scale(42)"/><use href="#oct" transform="translate(750 462) scale(42)"/>
    <use href="#oct" transform="translate(434 476) scale(30)"/><use href="#oct" transform="translate(716 566) scale(35)"/>
    <use href="#oct" transform="translate(406 573) scale(37)"/><use href="#oct" transform="translate(469 660) scale(30)"/>
    <use href="#oct" transform="translate(572 693) scale(42)"/><use href="#oct" transform="translate(691 683) scale(52)"/>
  </g>
  <polygon fill="url(#hubFill)" transform="translate(572 520) scale(86)" points="0.951,0.309 0.588,0.809 0,1 -0.588,0.809 -0.951,0.309 -0.951,-0.309 -0.588,-0.809 0,-1 0.588,-0.809 0.951,-0.309"/>
  <text x="572" y="528" text-anchor="middle" font-size="20" fill="#1f2126" font-weight="500">AUTO FOLLOW</text>
  <g fill="#9dd3fb" font-size="11.5" text-anchor="middle">
    <text x="572" y="317">INSTANT</text><text x="572" y="332">FOLLOW</text>
    <text x="461" y="374">FOLLOW ME</text><text x="665" y="395">500 DAY</text>
    <text x="750" y="467">100 DAY</text><text x="434" y="480">BACK</text>
    <text x="716" y="570">FOLLOW</text><text x="406" y="573">FOLLOW</text><text x="406" y="588">BACK</text>
    <text x="469" y="665">JIM</text><text x="572" y="700">BACK</text>
    <text x="692" y="683">INSTANT</text><text x="692" y="698">FOLLOW</text>
  </g>
</svg>

<div class="abs mode-toggle">
  <svg width="181" height="30" viewBox="0 0 181 30" font-family="Cabin, sans-serif" font-size="9">
    <defs><linearGradient id="basicFill" x1="0" y1="0" x2="0" y2="1"><stop offset="0" stop-color="#c4e6ff"/><stop offset="1" stop-color="#8cc8f4"/></linearGradient></defs>
    <rect width="181" height="30" fill="url(#basicFill)"/>
    <polygon points="0,0 94,0 101,15 94,30 0,30" fill="var(--dark-2)"/>
    <text x="8" y="19" fill="#9dd3fb">ADVANCED MODE</text>
    <text x="108" y="19" fill="#1f2126">BASIC MODE</text>
  </svg>
</div>

<h2 class="abs section-title" style="left:240px;top:677px">Most hashtags user</h2>
<ol class="abs users">
  <li>1.&nbsp; Support</li><li>2.&nbsp; rennwaltz</li><li>3.&nbsp; QTBrawler</li>
  <li>4.&nbsp; stillroamingtho</li><li>5.&nbsp; blakeharrow</li><li>6.&nbsp; Rios_Madre</li>
</ol>
<svg class="abs chart" viewBox="495 895 375 235" font-family="Cabin, sans-serif">
  <g stroke="#c6c6c6" stroke-width="2" fill="none">
    <line x1="516" y1="900" x2="516" y2="1125"/><polyline points="509,908 516,900 523,908"/>
    <line x1="508" y1="1113" x2="862" y2="1113"/><polyline points="853,1106 862,1113 853,1120"/>
  </g>
  <polyline fill="none" stroke="var(--chart)" stroke-width="2" points="517,985 537,955 550,997 567,933 593,1017 618,955 654,1048 685,912 738,1082 763,992 770,1017 787,956 798,996 822,930 856,1013"/>
  <circle cx="685" cy="913" r="8" fill="#bdbdbd"/>
  <text x="697" y="917" font-size="11" fill="#1f2126">Support - 1,725,892 followers</text>
  <text x="682" y="1127" font-size="11" fill="#1f2126" text-anchor="middle">user specialization for this hashtag</text>
  <text transform="translate(510 1010) rotate(-90)" font-size="11" fill="#1f2126" text-anchor="middle">user influence for this hashtag</text>
</svg>

<h2 class="abs section-title" style="left:734px;top:146px">Follow us on</h2>
<div class="abs follow-btn" style="top:188px"><i class="ico"></i><span>Chirpline</span></div>
<div class="abs follow-btn" style="top:218px"><i class="ico"></i><span>Friendwall</span></div>
<div class="abs follow-btn" style="top:248px"><i class="ico"></i><span>Circlespace</span></div>
<div class="abs followers" style="top:188px">24,587 followers</div>
<div class="abs followers" style="top:218px">24,587 followers</div>
<div class="abs followers" style="top:248px">24,587 followers</div>

<div class="abs counter-box"></div>
<p class="abs" style="left:745px;top:290px;font-size:10px">Hashtags found so far</p>
<div class="abs digit" style="left:749px">1</div><div class="abs digit" style="left:772px">0</div>
<div class="abs digit" style="left:794px">4</div><div class="abs digit" style="left:817px">5</div>
<div class="abs digit" style="left:839px">7</div><div class="abs digit" style="left:862px">0</div>
<div class="abs digit" style="left:884px">2</div><div class="abs digit" style="left:907px">3</div>
<div class="abs digit" style="left:929px">9</div>
<p class="abs" style="left:745px;top:343px;font-size:10px">in 5,004,267 tweets</p>

<div class="abs" style="left:736px;top:399px;width:12px;height:12px;border-radius:50%;background:var(--accent)"></div>
<h2 class="abs section-title" style="left:757px;top:393px">Recent Tweets</h2>

<div class="abs avatar" role="img" aria-label="Profile photo of Laura" style="top:438px;background:linear-gradient(#e8e8e8,#a9a9a9)"></div>
<div class="abs avatar-name" style="top:473px">Laura</div>
<div class="abs bubble" style="top:435px">At norvo communication, we believe results are what matter most. With over 15 years<em>2 minutes ago</em></div>

<div class="abs avatar" role="img" aria-label="Profile photo of Kylie" style="top:498px;background:linear-gradient(#c9a98c,#6e4b35)"></div>
<div class="abs avatar-name" style="top:533px">Kylie</div>
<div class="abs bubble" style="top:495px">At norvo communication, we believe results are what matter most. With over 15 years<em>2 minutes ago</em></div>

<div class="abs avatar" role="img" aria-label="Profile photo of Kevin" style="top:558px;background:linear-gradient(#8a7a70,#2f2a2a)"></div>
<div class="abs avatar-name" style="top:593px">Kevin</div>
<div class="abs bubble" style="top:555px">At norvo communication, we believe results are what matter most. With over 15 years<em>2 minutes ago</em></div>

<div class="abs avatar" role="img" aria-label="Profile photo of Mikey" style="top:618px;background:linear-gradient(#9cc4ee,#2e5fb0)"></div>
<div class="abs avatar-name" style="top:653px">Mikey</div>
<div class="abs bubble" style="top:615px">At norvo communication, we believe results are what matter most. With over 15 years<em>2 minutes ago</em></div>

<div class="abs avatar" role="img" aria-label="Profile photo of Cathrine" style="top:678px;background:linear-gradient(#e8e8e8,#a9a9a9)"></div>
<div class="abs avatar-name" style="top:713px">Cathrine</div>
<div class="abs bubble" style="top:675px">At norvo communication, we believe results are what matter most. With over 15 years<em>2 minutes ago</em></div>

<div class="abs avatar" role="img" aria-label="Profile photo of Rose" style="top:738px;background:linear-gradient(#c9a98c,#6e4b35)"></div>
<div class="abs avatar-name" style="top:773px">Rose</div>
<div class="abs bubble" style="top:735px">At norvo communication, we believe results are what matter most. With over 15 years<em>2 minutes ago</em></div>

<div class="abs avatar" role="img" aria-label="Profile photo of Richard" style="top:798px;background:linear-gradient(#8a7a70,#2f2a2a)"></div>
<div class="abs avatar-name" style="top:833px">Richard</div>
<div class="abs bubble" style="top:795px">At norvo communication, we believe results are what matter most. With over 15 years<em>2 minutes ago</em></div>

<div class="abs avatar" role="img" aria-label="Profile photo of Richard" style="top:858px;background:linear-gradient(#8a7a70,#2f2a2a)"></div>
<div class="abs avatar-name" style="top:893px">Richard</div>
<div class="abs bubble" style="top:855px">At norvo communication, we believe results are what matter most. With over 15 years<em>2 minutes ago</em></div>

<div class="abs footer-fade"></div>
<footer class="abs footer">
  <span class="abs" style="left:240px;top:16px">Copyright (c) 2011-2012 Velmoria Ltd</span>
  <span class="abs" style="left:802px;top:16px">Terms &amp; Condition&nbsp;&nbsp;&nbsp; |&nbsp;&nbsp;&nbsp; Privacy Policy</span>
</footer>
</body>
</html>
```